Webdesign für HALDEN STAHLWERK
Zielgruppe
Valkorin ist Ihr leistungsstarker und zuverlässiger Partner im Bereich Metallverarbeitung. Seit unserer Firmengründung im Jahr 2001 ist unser inhabergeführtes Unternehmen in Varnholm bei Kessbrück kontinuierlich gewachsen und beschäftigt derzeit 20 engagierte und qualifizierte Mitarbeiter.
Mit der Einweihung unserer neuen Fertigungshalle 2010 haben wir unsere Produktionsfläche auf 1.400 m2 vergrößert und können Ihnen nun einen noch umfassenderen Service anbieten.
Von der CNC-gesteuerten Teilefertigung bis zu modernsten Schweiß-, Schneid-, und Bearbeitungsanlagen – für die Realisierung Ihrer individuellen Wünsche steht uns ein innovativer Maschinenpark zur Verfügung. Wir fertigen zuverlässig und termingerecht nach Ihren Plänen oder übernehmen bei Bedarf auch die gesamte Abwicklung Ihres Projektes – alles made in germany!
Das Unternehmen spricht ausschließlich B2B Kunden an.
Die Hauptleistungsbereiche sind:
- Stahl- und Palettenbau
- Blechbearbeitung
- Edelstahlbearbeitung
- Mechanische Fertigung
Aufgabenstellung
- Mitlaufende Kontaktleiste
- Integration der Social Media Kanäle
- Sehr modernes Auftreten
- Industrielles Design
- Verlinkung zum Partnerunternehmen https://www.valkorin-beispiel.de/ias/index.html

```html
<!DOCTYPE html>
<html lang="de">
<head>
<meta charset="utf-8">
<title>Valkorin – Metallverarbeitung</title>
<link href="https://fonts.googleapis.com/css2?family=Kanit:wght@300;400;500;600;700&display=swap" rel="stylesheet">
<style>
:root{
  --blue:#0b3a78;
  --blue-dark:#082c5c;
  --ink:#1a1a1a;
  --text:#666;
  --dark:#121a26;
  --grey:#c6c6c6;
  --light:#f0f0f0;
  --white:#fff;
}
*{margin:0;padding:0;box-sizing:border-box}
html,body{width:1200px;height:2991px;overflow:hidden}
body{font-family:'Kanit',sans-serif;color:var(--ink);background:var(--white);position:relative}
h2{font-weight:600;font-size:21px;line-height:1.25;text-transform:uppercase;color:var(--ink)}
.rule{display:block;width:148px;height:4px;background:var(--blue);margin-top:8px}
p{font-weight:300;font-size:11px;line-height:18px;color:var(--text)}

.topbar{position:absolute;top:0;left:0;width:1200px;height:35px;background:var(--white);display:flex;gap:38px;align-items:center;padding-left:64px;font-size:11px;font-weight:500}
.topbar span{display:flex;align-items:center;gap:6px}
.topbar svg{width:14px;height:14px}

.hero{position:absolute;top:35px;left:0;width:1200px;height:414px;background:linear-gradient(100deg,#3c3a34 0%,#6b5a48 35%,#8a5a45 50%,#5c6064 70%,#3d4044 100%)}
.brand{position:absolute;top:40px;left:64px;display:flex;align-items:center;gap:8px;font-weight:700;font-size:40px;color:#1c1c1c;letter-spacing:-1px}
.brand i{width:12px;height:12px;background:var(--blue);display:block}
.nav{position:absolute;top:33px;left:418px;right:0;height:45px;display:flex}
.nav ul{list-style:none;background:var(--white);display:flex;flex:1;padding-left:17px}
.nav li{font-weight:600;font-size:15px;padding:0 17px;line-height:45px;position:relative}
.nav li.active::after{content:"";position:absolute;left:17px;right:17px;bottom:0;height:4px;background:var(--blue)}
.nav .call{background:var(--blue);color:var(--white);width:195px;display:flex;align-items:center;justify-content:center;gap:7px;font-size:12px;font-weight:500}
.hero h1{position:absolute;top:187px;left:64px;color:var(--white);font-size:29px;line-height:36px;font-weight:700}
.hero .lead{position:absolute;top:278px;left:64px;color:var(--white);font-size:12px;line-height:14px;font-weight:400}
.btn{display:inline-flex;align-items:center;justify-content:center;height:26px;border-radius:13px;font-size:9px;font-weight:500;text-transform:uppercase}
.btn.blue{background:var(--blue);color:var(--white)}
.btn.white{background:var(--white);color:var(--blue)}
.hero .btns{position:absolute;top:327px;left:64px;display:flex;gap:22px}
.social{position:absolute;top:206px;right:0;width:45px;height:134px;background:var(--white);border-radius:5px 0 0 5px;display:flex;flex-direction:column;justify-content:space-around;align-items:center;box-shadow:0 2px 8px rgba(0,0,0,.15)}
.social i{width:16px;height:16px;border-radius:50%;background:var(--blue-dark);display:block}

.welcome-text{position:absolute;top:522px;left:64px;width:450px}
.welcome-text p{margin-top:30px}
.welcome-text .sub{font-weight:600;color:#444}
.ticks{list-style:none;font-weight:300;font-size:11px;line-height:18px;color:var(--text)}
.ticks li{display:flex;align-items:center;gap:6px}
.welcome-img{position:absolute;top:512px;left:649px;width:489px;height:367px;background:linear-gradient(120deg,#1d3d8a 0%,#2a4fb0 45%,#1b2030 70%,#3a3f48 100%)}

.products{position:absolute;top:917px;left:0;width:1200px;height:480px;background:linear-gradient(180deg,#1b2433,#0e141e)}
.products h2{color:var(--white);text-align:center;position:absolute;top:48px;width:100%}
.products .rule{position:absolute;top:86px;left:512px;width:177px;background:var(--white)}
.card{position:absolute;top:141px;width:522px;height:211px;display:flex}
.card .photo{width:282px;background:linear-gradient(135deg,#3a4a6a,#7a5a40 55%,#2a3040)}
.card .body{flex:1;background:var(--blue);padding:36px 22px;color:var(--white)}
.card h3{font-size:12px;font-weight:600}
.card .short{display:block;width:50px;height:3px;background:var(--white);margin:7px 0 18px}
.card p{color:var(--white);line-height:18px}
.card .more{margin-top:12px;font-size:12px;display:flex;gap:8px;align-items:center}
.card .more span{border-bottom:1px solid var(--white)}
.arrow-btn{position:absolute;top:231px;width:34px;height:34px;background:var(--blue);display:flex;align-items:center;justify-content:center}
.counter{position:absolute;top:360px;right:63px;color:var(--white);font-size:10px}
.quote{position:absolute;top:400px;width:100%;text-align:center;color:var(--white);font-size:11px;font-style:italic;font-weight:300;line-height:18px}

.company-img{position:absolute;top:1461px;left:64px;width:489px;height:367px;background:linear-gradient(120deg,#2a4a8a 0%,#5d7aa8 40%,#9aa0a6 60%,#50555c 100%)}
.company-text{position:absolute;top:1503px;left:649px;width:450px}
.company-text p{margin-top:30px}
.company-text .bold{font-weight:600;color:#555;margin-top:8px}
.company-text .btn{width:139px;margin-top:52px}

.quals{position:absolute;top:1882px;left:0;width:601px;height:260px;background:var(--blue)}
.quals .frame{position:absolute;top:41px;left:64px;width:488px;height:177px;border:2px solid var(--white);padding:26px 22px;color:var(--white)}
.quals h2,.partner h2{font-size:20px}
.quals h2{color:var(--white)}
.quals p{color:var(--white);margin-top:6px}
.quals .more{margin-top:18px;font-size:11px;display:flex;gap:8px;align-items:center}
.quals .more span{border-bottom:2px solid var(--white);padding-bottom:4px}
.partner{position:absolute;top:1882px;left:601px;width:599px;height:260px;background:var(--grey);padding:70px 48px}
.partner p{color:#333;margin-top:6px}
.partner .mark{margin-top:20px;display:flex;align-items:center;gap:8px}
.partner .mark i{width:40px;height:24px;background:var(--blue);display:block}
.partner .mark b{width:86px;height:14px;background:#2d4f87;display:block}

.maker h2{position:absolute;top:2180px;width:1200px;text-align:center;font-size:20px}
.maker .rule{position:absolute;top:2216px;left:494px;width:177px}
.cert{position:absolute;top:2272px;width:488px;height:103px;border:1px solid #ddd;display:flex;align-items:center;padding:0 22px;gap:40px}
.cert .badge{width:122px;height:34px;background:#2b74c4;border-radius:3px}
.cert .badge.alt{background:#5b6f93;width:120px}
.cert h4{font-size:10px;font-weight:600}
.cert p{font-size:9px;line-height:15px;color:#333}

.adv{position:absolute;top:2437px;left:0;width:1200px;height:337px;background:var(--light)}
.adv h2{position:absolute;top:68px;left:64px;font-size:20px}
.item{position:absolute;width:440px;display:flex;gap:23px}
.item .ic{width:48px;height:48px;border:1px solid #bbb;border-radius:50%;display:flex;align-items:center;justify-content:center;flex:none;background:var(--white)}
.item h3{font-size:15px;font-weight:600;color:#777}
.item p{font-size:10px;line-height:14px;margin-top:6px}

.footer{position:absolute;top:2774px;left:0;width:1200px;height:217px;background:linear-gradient(180deg,#1a1e26,#0e1116);color:var(--white);font-size:10px;font-weight:500}
.footer h5{font-size:12px;font-weight:600;margin-bottom:12px}
.col{position:absolute;top:25px;line-height:15px}
.col .row{display:flex;gap:14px}
.col .row svg{flex:none;margin-top:2px}
.copy{position:absolute;top:25px;right:63px;font-size:12px;font-weight:600}
</style>
</head>
<body>

<div class="topbar">
  <span><svg viewBox="0 0 14 14"><path d="M1 13h12M3 13V5l4-3 4 3v8" stroke="#0b3a78" fill="none" stroke-width="1.3"/></svg>Stahl- und Palettenbau</span>
  <span><svg viewBox="0 0 14 14"><rect x="2" y="2" width="10" height="10" stroke="#0b3a78" fill="none" stroke-width="1.3"/></svg>Blechbearbeitung</span>
  <span><svg viewBox="0 0 14 14"><path d="M2 4h10M2 7h7M2 10h10" stroke="#0b3a78" stroke-width="1.3"/></svg>Edelstahlbearbeitung</span>
  <span><svg viewBox="0 0 14 14"><circle cx="7" cy="4" r="2.5" stroke="#0b3a78" fill="none" stroke-width="1.3"/><path d="M2 13c0-3 2-5 5-5s5 2 5 5" stroke="#0b3a78" fill="none" stroke-width="1.3"/></svg>Mechanische Fertigung</span>
</div>

<header class="hero" role="img" aria-label="Foto einer Industriemaschine in der Fertigungshalle">
  <div class="brand"><i></i>VALKORIN</div>
  <nav class="nav">
    <ul><li class="active">HOME</li><li>PRODUKTE</li><li>FERTIGUNG</li><li>QUALIFIKATION</li><li>KONTAKT</li></ul>
    <div class="call"><svg width="12" height="12" viewBox="0 0 12 12"><path d="M2 1l2 0 1 3-1.5 1a6 6 0 003.5 3.5L8 7l3 1v2c-5 1-10-4-9-9z" fill="#fff"/></svg>+49 (0) 3721 / 540 210 7</div>
  </nav>
  <h1>Ihr zuverlässiger Partner im<br>Bereich Metallverarbeitung</h1>
  <div class="lead">Bei Fragen zu unserem Leistungsangebot sind wir nur<br>einen Anruf oder eine E-Mail entfernt.</div>
  <div class="btns"><span class="btn blue" style="width:86px">Kontakt</span><span class="btn white" style="width:152px">+49 (0)3721 / 540 210 7</span></div>
  <div class="social"><i></i><i></i><i></i></div>
</header>

<section class="welcome-text">
  <h2>Herzlich willkommen bei Valkorin<br>in Varnholm</h2><span class="rule"></span>
  <p>Valkorin ist Ihr leistungsstarker und zuverlässiger Partner im Bereich Metallverarbeitung. Seit unserer Firmengründung im Jahr 2001 ist unser inhabergeführtes Unternehmen in Varnholm bei Kessbrück kontinuierlich gewachsen und beschäftigt derzeit 20 engagierte und qualifizierte Mitarbeiter.</p>
  <p class="sub" style="margin-top:6px">Unsere Hauptleistungsbereiche sind:</p>
  <ul class="ticks">
    <li><svg width="14" height="10" viewBox="0 0 14 10"><path d="M1 5l4 4 8-8" stroke="#0b3a78" stroke-width="2" fill="none"/></svg>Stahl- und Palettenbau</li>
    <li><svg width="14" height="10" viewBox="0 0 14 10"><path d="M1 5l4 4 8-8" stroke="#0b3a78" stroke-width="2" fill="none"/></svg>Blechbearbeitung</li>
    <li><svg width="14" height="10" viewBox="0 0 14 10"><path d="M1 5l4 4 8-8" stroke="#0b3a78" stroke-width="2" fill="none"/></svg>Edelstahlbearbeitung</li>
    <li><svg width="14" height="10" viewBox="0 0 14 10"><path d="M1 5l4 4 8-8" stroke="#0b3a78" stroke-width="2" fill="none"/></svg>Mechanische Fertigung</li>
  </ul>
  <p style="margin-top:18px">Mit der Einweihung unserer neuen Fertigungshalle 2010 haben wir unsere Produktionsfläche auf 1.400 m² vergrößert und können Ihnen nun einen noch umfassenderen Service anbieten.</p>
</section>
<div class="welcome-img" role="img" aria-label="Foto eines Schweißers mit Schutzhelm bei der Arbeit, blau getönt"></div>

<section class="products">
  <h2>Unsere Produkte</h2><span class="rule"></span>
  <div class="arrow-btn" style="left:24px"><svg width="8" height="14" viewBox="0 0 8 14"><path d="M7 1L1 7l6 6" stroke="#fff" fill="none"/></svg></div>
  <article class="card" style="left:64px">
    <div class="photo" role="img" aria-label="Foto eines Arbeiters mit Winkelschleifer und Funkenflug"></div>
    <div class="body"><h3>LADUNGSTRÄGER</h3><span class="short"></span>
      <p>Gut aliquip ex ea commodo consequat. Duis aute irure dolor in reprehenderit in voluptate</p>
      <div class="more"><span>Mehr erfahren</span><svg width="18" height="6" viewBox="0 0 18 6"><path d="M0 3h17M14 0l3 3-3 3" stroke="#fff" fill="none"/></svg></div></div>
  </article>
  <article class="card" style="left:616px">
    <div class="photo" role="img" aria-label="Foto eines Arbeiters mit Winkelschleifer und Funkenflug"></div>
    <div class="body"><h3>SPEZIALKONSTRUKTIONEN</h3><span class="short"></span>
      <p>Gut aliquip ex ea commodo consequat. Duis aute irure dolor in reprehenderit in voluptate</p>
      <div class="more"><span>Mehr erfahren</span><svg width="18" height="6" viewBox="0 0 18 6"><path d="M0 3h17M14 0l3 3-3 3" stroke="#fff" fill="none"/></svg></div></div>
  </article>
  <div class="arrow-btn" style="right:23px"><svg width="8" height="14" viewBox="0 0 8 14"><path d="M1 1l6 6-6 6" stroke="#fff" fill="none"/></svg></div>
  <div class="counter">2 / 10</div>
  <div class="quote">"Erfahrung, Wissen und Können sind der Garant für unsere Produkte "made in germany"! Ob Einzelstück oder Großserienfertigung –<br>wir fertigen Stahlerzeugnisse mit größten Ansprüchen an Qualität und Preis-Leistungsverhältnis."</div>
</section>

<div class="company-img" role="img" aria-label="Foto gebogener Edelstahlbleche, teilweise blau getönt"></div>
<section class="company-text">
  <h2>Das Unternehmen<br>für Metallverarbeitung</h2>
  <p>Lorem ipsum dolor sit amet, consectetur adipisicing elit, sed do eiusmod tempor incididunt ut labore et dolore magna aliqua. Ut enim ad minim veniam, quis nostrud exercitation ullamco laboris nisi ut aliquip ex ea commodo consequat.</p>
  <p class="bold">Excepteur sint occaecat cupidatat non proident, sunt in culpa qui officia deserunt mollit anim id est ladrum. Sed ut perspiciatis unde omnis iste natus error sit voluptatem ast laboru pers iciati.</p>
  <span class="btn blue">Unsere Produkte</span>
</section>

<section class="quals"><div class="frame">
  <h2>Unsere Qualifikationen</h2>
  <p>Lorem ipsum dolor sit amet, consectetur adipiscing elit, sed do eiusmod tempor incididunt ut labore et dolore magna aliqua. Quis ipsum suspendisse ultrices gravida. Risus commodo viverra maecenas accumsan lacus vel facilisis.</p>
  <div class="more"><span>Zu den Qualifikationen</span><svg width="18" height="6" viewBox="0 0 18 6"><path d="M0 3h17M14 0l3 3-3 3" stroke="#fff" fill="none"/></svg></div>
</div></section>
<section class="partner">
  <h2>Unser Partnerunternehmen</h2>
  <p>Alder Anlagentechnik ist Ihr leistungsstarker und zuverlässiger Partner für Aufzugmontage, Fahr-treppenmontage, Fahrsteigmontage und die Montage von Fassadenliften und Befahranlagen sowie deren Wartung.</p>
  <div class="mark"><i></i><b></b></div>
</section>

<section class="maker">
  <h2>Hersteller Qualifikationen</h2><span class="rule"></span>
  <div class="cert" style="left:64px"><div class="badge"></div><div><h4>Zertifikat</h4><p>Für tragende Konstruktionen in allen Arten von<br>Bauwerken</p></div></div>
  <div class="cert" style="left:649px"><div class="badge alt"></div><div><h4>EG-Zertifikat</h4><p>Werkseigene Produktionskontrolle und<br>Schweißzertifikat für Stahlbauten gemäß EN 1090</p></div></div>
</section>

<section class="adv">
  <h2>Ihre Vorteile im Überblick</h2>
  <div class="item" style="top:133px;left:64px"><div class="ic"><svg width="18" height="18" viewBox="0 0 18 18"><circle cx="9" cy="8" r="4" stroke="#0b3a78" fill="none"/><path d="M7 14h4" stroke="#0b3a78"/></svg></div><div><h3>HERSTELLER-QUALIFIKATIONEN</h3><p>Lorem ipsum dolor sit amet, consetetur sadipscing elitr, sed diam nonumy eirmod tempor invidunt ut labore et dolore magna alidiam voluptua</p></div></div>
  <div class="item" style="top:133px;left:649px"><div class="ic"><svg width="18" height="18" viewBox="0 0 18 18"><path d="M3 8h3v7H3zM6 8l3-5c2 0 2 2 1 4h4v4l-2 4H6" stroke="#0b3a78" fill="none"/></svg></div><div><h3>Interne Qualitätssicherung</h3><p>Lorem ipsum dolor sit amet, consetetur sadipscing elitr, sed diam nonumy eirmod tempor invidunt ut labore et dolore magna alidiam voluptua</p></div></div>
  <div class="item" style="top:208px;left:64px"><div class="ic"><svg width="18" height="18" viewBox="0 0 18 18"><rect x="2" y="4" width="14" height="12" stroke="#0b3a78" fill="none"/><path d="M2 8h14" stroke="#0b3a78"/></svg></div><div><h3>Realisierung individueller Wünsche</h3><p>Lorem ipsum dolor sit amet, consetetur sadipscing elitr, sed diam nonumy eirmod tempor invidunt ut labore et dolore magna alidiam voluptua</p></div></div>
  <div class="item" style="top:208px;left:649px"><div class="ic"><svg width="18" height="18" viewBox="0 0 18 18"><path d="M9 2l2 5h5l-4 3 2 5-5-3-5 3 2-5-4-3h5z" stroke="#0b3a78" fill="none"/></svg></div><div><h3>Hochmoderne Fertigungshalle</h3><p>Lorem ipsum dolor sit amet, consetetur sadipscing elitr, sed diam nonumy eirmod tempor invidunt ut labore et dolore magna alidiam voluptua</p></div></div>
</section>

<footer class="footer">
  <div class="col" style="left:64px"><h5>So erreichen Sie uns</h5>
    <div class="row"><svg width="8" height="10" viewBox="0 0 8 10"><path d="M4 10C1 6 0 5 0 4a4 4 0 018 0c0 1-1 2-4 6z" fill="#2b6fd1"/></svg><div>VALKORIN<br>Inhaber: Lars Weidner<br>Lindenweg 12<br>07712 Varnholm</div></div>
    <div class="row" style="margin-top:8px"><svg width="9" height="9" viewBox="0 0 12 12"><path d="M2 1l2 0 1 3-1.5 1a6 6 0 003.5 3.5L8 7l3 1v2c-5 1-10-4-9-9z" fill="#2b6fd1"/></svg><div>Telefon: 03721 / 540 210 7<br>Telefax: 03721 / 540 210 9</div></div>
    <div class="row"><svg width="9" height="7" viewBox="0 0 9 7"><rect width="9" height="7" fill="#2b6fd1"/></svg><div>E-Mail: info@valkorin-beispiel.de</div></div>
  </div>
  <div class="col" style="left:352px"><h5>Wichtige Links</h5>Home<br>Produkte<br>Fertigung<br>Qualifikation<br>Kontakt</div>
  <div class="col" style="left:614px"><h5>Rechtliches</h5>Impressum<br>AGB<br>Datenschutz</div>
  <div class="copy">© 2023 VALKORIN | Alle Rechte vorbehalten</div>
</footer>

</body>
</html>
```